Business Card Design

It's an investment advisory service for individuals with all there investment needs. Also financial consulting to businesses and governmental agencies on retirement plans etc. It's personalized not commoditized help. Should show strength, knowledge and money orientation.

Reason: Will be out of town setting up office.

Reason: waiting for the 2/3rds of group to vote

Reason: only half the votes are in, I'm calling and getting verbals, but at this time we are down to 2 designs.

Industry/Entity Type

Investment

Contact Information for Business Card

B. Rel K. Financial Consulting and Wealth Management, Berislav Mike Holcek, 5172 Pasadena Loma Verde, San Diego, CA 94417-6381, Registered Investment Advisor

Requirements
Nice to have
• Something money oriented

```html
<!DOCTYPE html>
<html lang="en">
<head>
<meta charset="utf-8">
<title>B. Rel K. Business Card</title>
<link rel="stylesheet" href="https://fonts.googleapis.com/css2?family=Fira+Sans:wght@400;700&family=Archivo+Black&display=swap">
<style>
  :root {
    --backdrop: #e6e6e6;
    --brand-blue: #17649a;
    --brand-lime: #a6cf2a;
    --lime-light: #b9dc36;
    --ink: #1b1b1b;
    --olive-text: #4d5a12;
    --white: #ffffff;
    --coin-dark: #3a3317;
    --coin-gold: #8a7a2e;
  }
  * { margin: 0; padding: 0; box-sizing: border-box; }
  html, body { width: 1200px; height: 1200px; overflow: hidden; }
  body {
    background: var(--backdrop);
    display: flex;
    align-items: center;
    justify-content: center;
    font-family: "Fira Sans", Arial, sans-serif;
  }
  .business-card {
    position: relative;
    width: 1050px;
    height: 600px;
    background: var(--brand-lime);
    overflow: hidden;
    box-shadow: 0 10px 30px rgba(0,0,0,0.18);
  }
  .top-band {
    position: absolute;
    left: 0; top: 0;
    width: 100%; height: 290px;
    background: var(--brand-blue);
  }
  .brand-mark {
    position: absolute;
    left: 330px; top: 120px;
    display: flex;
    align-items: center;
    gap: 16px;
  }
  .brand-name {
    font-family: "Fira Sans", Arial, sans-serif;
    font-weight: 700;
    font-size: 76px;
    color: var(--brand-lime);
    line-height: 1;
  }
  .brand-dot {
    width: 42px; height: 42px;
    border-radius: 50%;
    background: var(--brand-lime);
  }
  .company-tag {
    position: absolute;
    left: 525px; top: 222px;
    width: 470px;
    padding: 10px 18px;
    background: var(--lime-light);
    font-family: "Archivo Black", Impact, sans-serif;
    font-size: 28px;
    line-height: 1.05;
    color: var(--ink);
    text-transform: uppercase;
  }
  .contact-block {
    position: absolute;
    left: 70px; top: 305px;
  }
  .person-name {
    font-weight: 700;
    font-size: 34px;
    color: var(--white);
  }
  .address {
    margin-top: 8px;
    font-size: 25px;
    line-height: 1.25;
    color: var(--olive-text);
  }
  .credentials {
    position: absolute;
    left: 470px; top: 350px;
    display: flex;
    align-items: flex-start;
    gap: 14px;
  }
  .divider {
    width: 2px; height: 84px;
    background: var(--white);
  }
  .role {
    font-size: 24px;
    color: var(--white);
  }
  .phone-list { margin-top: 6px; list-style: none; }
  .phone-list li {
    display: flex;
    align-items: center;
    gap: 10px;
    font-size: 22px;
    color: var(--ink);
    line-height: 1.35;
  }
  .phone-list svg { width: 20px; height: 20px; }
  .coin-field {
    position: absolute;
    left: 0; bottom: 0;
    width: 100%; height: 150px;
    background: linear-gradient(180deg, rgba(166,207,42,0) 0%, var(--coin-gold) 45%, var(--coin-dark) 100%);
  }
</style>
</head>
<body>
  <div class="business-card">
    <div class="top-band"></div>

    <div class="brand-mark">
      <span class="brand-name">B. Rel K.</span>
      <span class="brand-dot"></span>
    </div>

    <div class="company-tag">Financial Consulting and<br>Wealth Management</div>

    <div class="contact-block">
      <p class="person-name">Berislav Mike Holcek</p>
      <p class="address">5172 Pasadena Loma Verde,<br>San Diego, CA 94417-6381</p>
    </div>

    <div class="credentials">
      <div class="divider"></div>
      <div>
        <p class="role">Registered Investment Advisor</p>
        <ul class="phone-list">
          <li>
            <svg viewBox="0 0 20 20" aria-hidden="true"><rect x="2" y="5" width="16" height="12" rx="2" fill="#1b1b1b"/><rect x="5" y="2" width="10" height="5" rx="1" fill="#1b1b1b"/></svg>
            (xxx) xxx-xxxx
          </li>
          <li>
            <svg viewBox="0 0 20 20" aria-hidden="true"><rect x="5" y="1" width="10" height="18" rx="2" fill="#1b1b1b"/><rect x="7" y="4" width="6" height="9" fill="#a6cf2a"/></svg>
            xxxxxxxxxx
          </li>
        </ul>
      </div>
    </div>

    <div class="coin-field" role="img" aria-label="Illustration of stacked gold coins with small green sprouts growing between them"></div>
  </div>
</body>
</html>
```